Informational Site for Advanced Chemistry R&D

The company develops oxidation chemistry for air, water, fuel pollution controls. The site has been prototyped at www.velquaresearch.example. Take a look. Now, the task is to design it for eye-catching beauty with use of color, on-page scroll-driven color transition and parallax effects. Should capture the themes: high technology, wow it's beautiful, modern, uncluttered, clean urban environment.

Target Market(s)

China Environmentally Conscious Government and Industry,

Industry/Entity Type

It Company

Number of Pages Required

3 page

Font styles to use
Sans Serif

Requirements
Must have
• Parallax effects, desktop compatible, Rich, Modern, Simple, Graphic
Nice to have
• Mobile Phone Compatible
Should not have
• Flash, or anything that is slow to load or requires high bandwidth

```html
<!DOCTYPE html>
<html lang="en">
<head>
<meta charset="utf-8">
<title>Velquara — Environmental Pollution Management</title>
<link rel="stylesheet" href="https://fonts.googleapis.com/css2?family=Raleway:wght@500;600;700;800&family=Open+Sans:wght@400;600&display=swap">
<style>
:root{
  --blue:#1a73c4;
  --blue-deep:#0f5ea8;
  --blue-light:#2a8ee0;
  --ink:#2b2b2b;
  --text:#555b63;
  --grey-band:#e6e6e6;
  --footer:#262626;
  --white:#ffffff;
  --black:#111111;
}
*{box-sizing:border-box;margin:0;padding:0}
html,body{width:1200px;height:3087px;overflow:hidden;background:var(--white)}
body{position:relative;font-family:"Open Sans",Arial,sans-serif;color:var(--text)}
.abs{position:absolute}
h1,h2,h3,.brand,.nav a{font-family:"Raleway",Arial,sans-serif}

/* header */
.site-header{left:0;top:0;width:1200px;height:132px;background:var(--white)}
.brand{left:133px;top:20px;display:flex;align-items:center;gap:12px;font-size:30px;font-weight:700;color:var(--blue)}
.brand-dot{width:44px;height:44px;border-radius:50%;background:var(--blue)}
.top-contact{top:28px;right:133px;display:flex;gap:34px;font-size:15px;color:var(--ink)}
.top-contact span{display:flex;align-items:center;gap:14px}
.ring-ico{width:32px;height:32px;border:1.5px solid var(--blue);border-radius:50%;display:flex;align-items:center;justify-content:center}
.nav{top:88px;right:133px;display:flex;gap:44px;font-size:15px;font-weight:500}
.nav a{color:var(--ink);text-decoration:none;padding-bottom:20px;letter-spacing:.3px}
.nav a.active{color:var(--blue);border-bottom:4px solid var(--blue)}

/* hero */
.hero{left:0;top:132px;width:1200px;height:520px;background:linear-gradient(180deg,#3d8fd6 0%,#1c6fbf 55%,#175fa8 100%)}
.hero-scene{left:0;top:0;width:1200px;height:520px;background:linear-gradient(180deg,rgba(120,180,235,.35),rgba(20,90,170,.2))}
.hero h1{left:0;top:140px;width:1200px;text-align:center;color:var(--white);font-size:35px;font-weight:700;letter-spacing:2.5px}
.hero p{left:300px;top:200px;width:600px;text-align:center;color:var(--white);font-size:12.5px;line-height:24px}
.hero-btn{left:527px;top:284px;width:146px;height:52px;border:2px solid var(--white);color:var(--white);font-size:14px;font-weight:600;display:flex;align-items:center;justify-content:center;letter-spacing:.5px}
.dots{left:567px;top:432px;display:flex;gap:10px}
.dots i{width:6px;height:6px;border-radius:50%;background:rgba(255,255,255,.6)}
.dots i:first-child{background:var(--white)}
.hero-wave{left:0;top:560px;width:1200px;height:110px}

/* section headings */
.sec-title{left:0;width:1200px;text-align:center;font-size:28px;font-weight:700;color:var(--ink);letter-spacing:2px}

/* solutions */
.solution{width:300px;text-align:center}
.solution svg{display:block;margin:0 auto}
.solution h3{margin-top:36px;font-size:29px;font-weight:700;color:var(--blue);letter-spacing:2px}
.solution p{margin:20px auto 0;width:290px;font-size:12px;line-height:21px}
.more{display:block;margin-top:20px;font-size:12px;color:var(--blue)}

/* advanced oxidation */
.oxidation{left:0;top:1163px;width:1200px;height:437px;background:linear-gradient(180deg,var(--blue-light) 0%,#1f7fd0 60%,#1b72c0 100%)}
.oxidation h2{left:133px;top:66px;color:var(--white);font-size:28px;font-weight:700;letter-spacing:2.5px}
.ox-intro{left:133px;top:116px;width:460px;color:#dcecfb;font-size:11.5px;line-height:20px}
.ox-points{left:133px;top:174px;color:var(--white);font-size:14.5px;line-height:23px}
.ox-note{left:133px;top:245px;width:470px;color:#dcecfb;font-size:11.5px;line-height:20px}
.ox-btn{left:133px;top:322px;width:133px;height:46px;border-radius:23px;background:var(--black);color:var(--white);font-size:13px;display:flex;align-items:center;justify-content:center}
.ox-diagram{left:680px;top:40px;width:330px;height:345px;border-radius:40px;background:radial-gradient(circle at 45% 50%,rgba(255,215,60,.55),rgba(255,215,60,.15) 45%,rgba(255,255,255,0) 70%)}

/* products */
.product{width:230px;text-align:center}
.product svg{display:block;margin:0 auto}
.product h3{margin-top:18px;font-size:19px;line-height:29px;font-weight:700;color:var(--blue);letter-spacing:1.5px}
.product p{margin:20px auto 0;width:220px;font-size:12px;line-height:20px}

/* partners */
.partners{left:0;top:2176px;width:1200px;height:420px;background:var(--grey-band)}
.partner{top:124px;width:217px;height:140px;background:#f6f6f6;padding:12px}
.partner div{width:100%;height:100%;background:var(--white);display:flex;align-items:center;justify-content:center}
.partner i{display:block;width:86px;height:86px;border-radius:50%}

/* contact */
.contact-wave{left:0;top:2478px;width:1200px;height:120px}
.contact{left:0;top:2596px;width:1200px;height:420px;background:var(--blue)}
.contact h2{left:133px;top:0;color:var(--white);font-size:28px;font-weight:700;letter-spacing:1.5px}
.contact-copy{left:133px;top:44px;width:300px;color:#e6f1fb;font-size:12.5px;line-height:20px}
.contact-info{left:133px;top:130px;color:#e6f1fb;font-size:11px;line-height:24px}
.contact-info b{font-weight:400;letter-spacing:.5px}
.field-label{color:var(--white);font-size:11px}
.field{background:var(--white);height:35px}
.select-caret{right:12px;top:12px}
.send-btn{left:455px;top:325px;width:150px;height:40px;background:var(--black);color:var(--white);font-size:11px;display:flex;align-items:center;justify-content:center;gap:10px;letter-spacing:.5px}

/* footer */
.site-footer{left:0;top:3016px;width:1200px;height:71px;background:var(--footer)}
.site-footer p{left:133px;top:27px;color:#8a8a8a;font-size:11px}
.social{right:133px;top:24px;display:flex;gap:10px}
.social i{width:20px;height:20px;border-radius:50%;background:#8a8a8a}
</style>
</head>
<body>

<header class="site-header abs">
  <div class="brand abs"><span class="brand-dot"></span>Velquara</div>
  <div class="top-contact abs">
    <span><span class="ring-ico"><svg width="14" height="14" viewBox="0 0 24 24"><path d="M6.6 10.8a15 15 0 0 0 6.6 6.6l2.2-2.2c.3-.3.7-.4 1-.2 1.1.4 2.3.6 3.6.6.6 0 1 .4 1 1V20c0 .6-.4 1-1 1A17 17 0 0 1 3 4c0-.6.4-1 1-1h3.5c.6 0 1 .4 1 1 0 1.3.2 2.5.6 3.6.1.3 0 .7-.2 1z" fill="#1a73c4"/></svg></span>+1 555 014 2290</span>
    <span><span class="ring-ico"><svg width="14" height="12" viewBox="0 0 24 18"><rect x="1" y="1" width="22" height="16" fill="none" stroke="#1a73c4" stroke-width="2"/><path d="M1 1l11 9 11-9" fill="none" stroke="#1a73c4" stroke-width="2"/></svg></span>info@velquaresearch.example</span>
  </div>
  <nav class="nav abs">
    <a class="active">HOME</a><a>SOLUTIONS</a><a>TECHNOLOGY</a><a>PRODUCTS</a><a>PARTNERS</a><a>CONTACT</a>
  </nav>
</header>

<section class="hero abs">
  <div class="hero-scene abs" role="img" aria-label="Industrial plant with chimneys and storage tanks under a blue sky"></div>
  <h1 class="abs">ENVIRONMENTAL POLLUTION MANAGEMENT</h1>
  <p class="abs">Advanced Oxidation refers to a variety of techniques employing the Hydroxyl Radical, an energetic, highly reactive cousin of the water molecule.</p>
  <div class="hero-btn abs">VIEW DETAILS</div>
  <div class="dots abs"><i></i><i></i><i></i></div>
</section>
<svg class="hero-wave abs" viewBox="0 0 1200 110" preserveAspectRatio="none"><path d="M0 40 C 250 110 420 110 640 60 C 860 10 1030 0 1200 20 L1200 110 L0 110 Z" fill="#ffffff"/></svg>

<h2 class="sec-title abs" style="top:692px">SOLUTIONS</h2>

<div class="solution abs" style="left:120px;top:780px">
  <svg width="150" height="150" viewBox="0 0 150 150"><path d="M14 92 A62 62 0 0 1 137 66" fill="none" stroke="#1a73c4" stroke-width="14"/><path d="M128 110 A62 62 0 0 1 62 136" fill="none" stroke="#1a73c4" stroke-width="14"/><path d="M75 55 C68 67 64 73 64 80 a11 11 0 0 0 22 0 c0-7-4-13-11-25z" fill="#1a73c4"/></svg>
  <h3>WATER</h3>
  <p>Advanced Oxidation refers to a variety of techniques employing the Hydroxyl Radical, an energetic, highly reactive cousin of the water molecule</p>
  <span class="more">Read More</span>
</div>
<div class="solution abs" style="left:450px;top:780px">
  <svg width="150" height="150" viewBox="0 0 150 150"><path d="M14 92 A62 62 0 0 1 137 66" fill="none" stroke="#1a73c4" stroke-width="14"/><path d="M128 110 A62 62 0 0 1 62 136" fill="none" stroke="#1a73c4" stroke-width="14"/><path d="M54 74 L98 54 L86 98 L74 84 Z M74 84 L98 54" fill="none" stroke="#1a73c4" stroke-width="3" stroke-linejoin="round"/></svg>
  <h3>AIR</h3>
  <p>Advanced Oxidation refers to a variety of techniques employing the Hydroxyl Radical, an energetic, highly reactive cousin of the water molecule</p>
  <span class="more">Read More</span>
</div>
<div class="solution abs" style="left:777px;top:780px">
  <svg width="150" height="150" viewBox="0 0 150 150"><path d="M14 92 A62 62 0 0 1 137 66" fill="none" stroke="#1a73c4" stroke-width="14"/><path d="M128 110 A62 62 0 0 1 62 136" fill="none" stroke="#1a73c4" stroke-width="14"/><rect x="62" y="56" width="26" height="36" rx="3" fill="none" stroke="#1a73c4" stroke-width="3"/><path d="M68 56 l4-6 h10" fill="none" stroke="#1a73c4" stroke-width="3"/><path d="M69 66 l12 16 M81 66 l-12 16" stroke="#1a73c4" stroke-width="2.5"/></svg>
  <h3>FUEL</h3>
  <p>Advanced Oxidation refers to a variety of techniques employing the Hydroxyl Radical, an energetic, highly reactive cousin of the water molecule</p>
  <span class="more">Read More</span>
</div>

<section class="oxidation abs">
  <h2 class="abs">ADVANCED OXIDATION</h2>
  <p class="ox-intro abs">Advanced Oxidation refers to a variety of techniques employing the Hydroxyl Radical, an energetic, highly reactive cousin of the water molecule.</p>
  <p class="ox-points abs">To add oxygen to inorganic molecules<br>To remove hydrogen from organic molecules</p>
  <p class="ox-note abs">These transformations convert important industrial contaminants into reactive forms that can be captured or that disintegrate into harmless end products.</p>
  <div class="ox-btn abs">Learn More</div>
  <div class="ox-diagram abs" role="img" aria-label="Reaction diagram of the hydroxyl radical linked to contaminant molecules"></div>
</section>

<h2 class="sec-title abs" style="top:1648px">PRODUCTS</h2>

<div class="product abs" style="left:120px;top:1728px">
  <svg width="190" height="190" viewBox="0 0 190 190" role="img" aria-label="Refinery piping and valves"><circle cx="95" cy="95" r="70" fill="#5f7488"/><path d="M15 115 A82 82 0 0 1 176 80" fill="none" stroke="#1a73c4" stroke-width="16"/><path d="M165 140 A82 82 0 0 1 85 176" fill="none" stroke="#1a73c4" stroke-width="16"/></svg>
  <h3>FUEL OIL<br>DESULFURIZATION</h3>
  <p>Our proprietary low temperature and pressure advanced oxidation catalytic process reliably removes</p>
  <span class="more">Read More</span>
</div>
<div class="product abs" style="left:363px;top:1728px">
  <svg width="190" height="190" viewBox="0 0 190 190" role="img" aria-label="Laboratory work with chemical containers"><circle cx="95" cy="95" r="70" fill="#6a7d8e"/><path d="M15 115 A82 82 0 0 1 176 80" fill="none" stroke="#1a73c4" stroke-width="16"/><path d="M165 140 A82 82 0 0 1 85 176" fill="none" stroke="#1a73c4" stroke-width="16"/></svg>
  <h3>VOLATILE ORGANIC<br>COMPUNDS</h3>
  <p>Our proprietary low temperature and pressure advanced oxidation catalytic process reliably removes</p>
  <span class="more">Read More</span>
</div>
<div class="product abs" style="left:607px;top:1728px">
  <svg width="190" height="190" viewBox="0 0 190 190" role="img" aria-label="Smokestacks releasing flue gas"><circle cx="95" cy="95" r="70" fill="#4d5566"/><path d="M15 115 A82 82 0 0 1 176 80" fill="none" stroke="#1a73c4" stroke-width="16"/><path d="M165 140 A82 82 0 0 1 85 176" fill="none" stroke="#1a73c4" stroke-width="16"/></svg>
  <h3>FLUE GAS<br>SCRUBBING</h3>
  <p>Our proprietary low temperature and pressure advanced oxidation catalytic process reliably removes</p>
  <span class="more">Read More</span>
</div>
<div class="product abs" style="left:845px;top:1728px">
  <svg width="190" height="190" viewBox="0 0 190 190" role="img" aria-label="Wastewater outflow pipe"><circle cx="95" cy="95" r="70" fill="#7d6a4e"/><path d="M15 115 A82 82 0 0 1 176 80" fill="none" stroke="#1a73c4" stroke-width="16"/><path d="M165 140 A82 82 0 0 1 85 176" fill="none" stroke="#1a73c4" stroke-width="16"/></svg>
  <h3>WASTEWATER<br>TREATMENT</h3>
  <p>Our proprietary low temperature and pressure advanced oxidation catalytic process reliably removes</p>
  <span class="more">Read More</span>
</div>

<section class="partners abs">
  <h2 class="sec-title abs" style="top:46px">PARTNERS</h2>
  <div class="partner abs" style="left:133px"><div><i style="background:#1aa0c8;border-radius:12px;width:110px;height:50px"></i></div></div>
  <div class="partner abs" style="left:376px"><div><i style="background:#d84a2a"></i></div></div>
  <div class="partner abs" style="left:619px"><div><i style="background:#2b5e96"></i></div></div>
  <div class="partner abs" style="left:862px"><div><i style="background:#a3213a"></i></div></div>
</section>

<svg class="contact-wave abs" viewBox="0 0 1200 120" preserveAspectRatio="none"><path d="M0 70 C 180 -10 340 0 520 60 C 700 120 900 70 1200 20 L1200 120 L0 120 Z" fill="#1a73c4"/></svg>

<section class="contact abs">
  <h2 class="abs">CONTACT US</h2>
  <p class="contact-copy abs">We welcome inquiries regarding the licensing, distribution, and purchase of our products, systems, and technologies.</p>
  <div class="contact-info abs">
    <b>HEADQUARTERS</b><br>Velquara Research Corporation<br>Harbor Vale, New Jersey,<br>U.S.A.<br><br><b>GET IN TOUCH</b><br>
    <span style="display:flex;align-items:center;gap:10px"><svg width="10" height="10" viewBox="0 0 24 24"><path d="M6.6 10.8a15 15 0 0 0 6.6 6.6l2.2-2.2c.3-.3.7-.4 1-.2 1.1.4 2.3.6 3.6.6.6 0 1 .4 1 1V20c0 .6-.4 1-1 1A17 17 0 0 1 3 4c0-.6.4-1 1-1h3.5c.6 0 1 .4 1 1 0 1.3.2 2.5.6 3.6.1.3 0 .7-.2 1z" fill="#fff"/></svg>+1 555 014 2290</span>
    <span style="display:flex;align-items:center;gap:10px"><svg width="10" height="8" viewBox="0 0 24 18"><rect width="24" height="18" fill="#fff"/><path d="M0 0l12 9 12-9" fill="none" stroke="#1a73c4" stroke-width="2"/></svg>info@velquaresearch.example</span>
  </div>

  <span class="field-label abs" style="left:455px;top:4px">Full Name</span>
  <div class="field abs" style="left:455px;top:24px;width:295px"></div>
  <span class="field-label abs" style="left:773px;top:4px">Email</span>
  <div class="field abs" style="left:773px;top:24px;width:295px"></div>

  <span class="field-label abs" style="left:455px;top:84px">Phone Number</span>
  <div class="field abs" style="left:455px;top:104px;width:295px"><svg class="select-caret abs" width="12" height="8" viewBox="0 0 12 8"><path d="M1 1l5 5 5-5" fill="none" stroke="#999" stroke-width="1.5"/></svg></div>
  <span class="field-label abs" style="left:773px;top:84px">Company</span>
  <div class="field abs" style="left:773px;top:104px;width:295px"><svg class="select-caret abs" width="12" height="8" viewBox="0 0 12 8"><path d="M1 1l5 5 5-5" fill="none" stroke="#999" stroke-width="1.5"/></svg></div>

  <span class="field-label abs" style="left:455px;top:164px">Tell us about your project</span>
  <div class="field abs" style="left:455px;top:186px;width:613px;height:114px"></div>

  <div class="send-btn abs"><svg width="12" height="12" viewBox="0 0 24 24"><path d="M2 12L22 3l-6 19-4-8z" fill="#fff"/></svg>SEND MESSAGE</div>
</section>

<footer class="site-footer abs">
  <p class="abs">Copyright 2016 velquaresearch.example | All Right Reserved</p>
  <div class="social abs"><i></i><i></i><i></i><i></i><i></i></div>
</footer>

</body>
</html>
```